Business Card - Tidal Lanes

Need Business Card design for company named Tidal Lanes. Software development focused mainly on Brindle Orvix & Zelt Apps. I've attached our logo with both a black and white background. Please add trademark symbol to logo when using.

```html
<!DOCTYPE html>
<html lang="en">
<head>
<meta charset="utf-8">
<title>Tidal Lanes – Business Card</title>
<link rel="stylesheet" href="https://fonts.googleapis.com/css2?family=Ubuntu:wght@500;700&family=Open+Sans:wght@400;600;700&display=swap">
<style>
  :root {
    --backdrop: #e4e5ea;
    --card-black: #0b0b0b;
    --ink-white: #ffffff;
    --accent-orange: #f29a2e;
    --band-yellow: #f8c51b;
    --band-orange: #f39a30;
    --stripe-red: #d8262b;
    --address-ink: #3a2405;
  }
  * { box-sizing: border-box; margin: 0; padding: 0; }
  html, body {
    width: 1200px; height: 987px; overflow: hidden;
    background: var(--backdrop);
  }
  .canvas {
    position: relative; width: 1200px; height: 987px;
    display: flex; flex-direction: column; align-items: center; justify-content: center; gap: 44px;
  }
  .card {
    position: relative; width: 760px; height: 434px;
    background: var(--card-black); border-radius: 30px; overflow: hidden;
    box-shadow: 0 10px 28px rgba(0,0,0,0.18);
  }

  /* Back side */
  .card-back .brand-name {
    position: absolute; left: 0; right: 0; top: 150px; text-align: center;
    font-family: "Ubuntu", sans-serif; font-weight: 700; font-size: 92px;
    letter-spacing: -3px; color: var(--ink-white); line-height: 1;
  }
  .brand-name .tm { font-size: 0.3em; vertical-align: 1.9em; letter-spacing: 0; margin-left: 4px; }
  .card-back .web-address {
    position: absolute; left: 0; right: 0; top: 272px; text-align: center;
    font-family: "Open Sans", sans-serif; font-size: 20px; letter-spacing: 3px; color: #cfcfcf;
  }

  /* Front side */
  .front-band { position: absolute; inset: 0; }
  .card-front .brand-block {
    position: absolute; left: 70px; top: 150px; width: 270px; text-align: center;
  }
  .card-front .brand-mark-dot {
    display: block; width: 18px; height: 18px; border-radius: 50%;
    background: var(--ink-white); margin: 0 auto 14px;
  }
  .card-front .brand-name {
    font-family: "Ubuntu", sans-serif; font-weight: 700; font-size: 44px;
    letter-spacing: -2px; color: var(--ink-white); line-height: 1;
  }
  .divider {
    position: absolute; left: 385px; top: 108px; width: 2px; height: 150px;
    background: linear-gradient(to bottom, rgba(255,255,255,0), rgba(255,255,255,0.85) 40%, rgba(255,255,255,0));
  }
  .contact { position: absolute; left: 420px; top: 104px; font-family: "Open Sans", sans-serif; }
  .contact .person-name { font-weight: 700; font-size: 30px; color: var(--accent-orange); line-height: 1.1; }
  .contact .person-title { font-size: 20px; color: var(--ink-white); margin-bottom: 20px; }
  .contact .line { display: flex; align-items: center; gap: 12px; font-size: 24px; color: var(--ink-white); line-height: 1.6; }
  .contact .line svg { width: 22px; height: 22px; flex: none; }
  .address {
    position: absolute; left: 170px; top: 352px; white-space: nowrap;
    font-family: "Open Sans", sans-serif; font-weight: 600; font-size: 18px; line-height: 24px;
    color: var(--address-ink); transform: rotate(7deg); transform-origin: left center;
  }
</style>
</head>
<body>
<main class="canvas">

  <section class="card card-front" aria-label="Card front">
    <svg class="front-band" viewBox="0 0 760 434" preserveAspectRatio="none" aria-hidden="true">
      <defs>
        <linearGradient id="bandGradient" x1="0" y1="0" x2="1" y2="0">
          <stop offset="0" stop-color="#f8c51b"/>
          <stop offset="1" stop-color="#f39a30"/>
        </linearGradient>
      </defs>
      <path d="M0 262 C 90 262, 160 300, 290 316 C 420 332, 560 360, 690 434 L 0 434 Z" fill="#d8262b"/>
      <path d="M0 268 C 90 270, 160 306, 290 324 C 420 342, 550 370, 670 434 L 0 434 Z" fill="#0b0b0b"/>
      <path d="M0 274 C 90 276, 160 314, 290 332 C 420 350, 540 380, 650 434 L 0 434 Z" fill="url(#bandGradient)"/>
    </svg>

    <div class="brand-block">
      <span class="brand-mark-dot"></span>
      <p class="brand-name">Tidal Lanes<span class="tm">™</span></p>
    </div>

    <div class="divider"></div>

    <div class="contact">
      <p class="person-name">Your Name</p>
      <p class="person-title">Title</p>
      <p class="line">
        <svg viewBox="0 0 24 24" aria-hidden="true"><rect x="6" y="2" width="12" height="20" rx="2" fill="#f29a2e"/><rect x="8" y="5" width="8" height="7" fill="#0b0b0b"/><circle cx="12" cy="17" r="1.6" fill="#0b0b0b"/></svg>
        555-214-7730
      </p>
      <p class="line">
        <svg viewBox="0 0 24 24" aria-hidden="true"><path d="M2 9 C 6 4, 18 4, 22 9 L 19 11 L 16 9 L 8 9 L 5 11 Z" fill="#f29a2e"/><rect x="4" y="12" width="16" height="9" rx="2" fill="#f29a2e"/><circle cx="12" cy="16.5" r="2.2" fill="#0b0b0b"/></svg>
        555-368-1942
      </p>
    </div>

    <p class="address">4120 Harbor Rd, Seacliff, FL 30912</p>
  </section>

  <section class="card card-back" aria-label="Card back">
    <p class="brand-name">Tidal Lanes<span class="tm">™</span></p>
    <p class="web-address">www.tidallanes.com</p>
  </section>

</main>
</body>
</html>
```